Brightmill Data Works

Our company is about IT hardwares and IT solutions. IT hardware such as PC, RAMS, storage and servers. IT solutions such as project management, BA. We are also selling new technology too.

Target Market(s)

Consumer, Small to Medium Business, Corporate

Requirements
Must have
• The business card must have the following:
• Name:
• Title:
• Contact Number:
• Email address:
• Website:
• Color: Must match the logo color upgrade

```html
<!DOCTYPE html>
<html lang="en">
<head>
<meta charset="utf-8">
<title>Brightmill Data Works – Business Card</title>
<link rel="stylesheet" href="https://fonts.googleapis.com/css2?family=Open+Sans:wght@400;600&family=Rubik:wght@600;700&display=swap">
<style>
  :root {
    --backdrop: #666666;
    --card-white: #f6f6f6;
    --ink-dark: #444444;
    --ink-body: #333333;
    --brand-orange: #cc7a2c;
    --orange-light: #e29c48;
    --orange-deep: #c2662a;
    --divider: #c9c9c9;
    --white: #ffffff;
  }
  * { margin: 0; padding: 0; box-sizing: border-box; }
  html, body {
    width: 1200px; height: 802px; overflow: hidden;
    background: var(--backdrop);
  }
  .canvas { position: relative; width: 1200px; height: 802px; }
  .card {
    position: absolute; top: 274px;
    width: 443px; height: 265px;
  }
  .card--front { left: 136px; background: var(--card-white); }
  .card--back {
    left: 624px;
    background: radial-gradient(ellipse at 45% 35%, var(--orange-light) 0%, var(--brand-orange) 50%, var(--orange-deep) 100%);
  }

  .brand-block {
    position: absolute; left: 20px; top: 78px; width: 200px;
    text-align: center;
    font-family: "Rubik", sans-serif; font-weight: 700;
    color: var(--ink-dark);
  }
  .brand-mark {
    display: block; width: 22px; height: 22px; margin: 0 auto 10px;
    background: var(--brand-orange);
  }
  .brand-name { font-size: 25px; line-height: 1.05; letter-spacing: 0.5px; }
  .brand-name .sub { display: block; font-size: 14px; letter-spacing: 5px; margin-top: 4px; }

  .divider {
    position: absolute; left: 236px; top: 79px;
    width: 1px; height: 108px; background: var(--divider);
  }
  .contact {
    position: absolute; left: 256px; top: 78px;
    font-family: "Open Sans", sans-serif; color: var(--ink-body);
  }
  .contact__name {
    font-size: 16px; color: var(--brand-orange); font-weight: 400;
    line-height: 1.1; letter-spacing: 0.2px;
  }
  .contact__title { font-size: 13px; line-height: 1.2; margin-left: 1px; }
  .contact__list { list-style: none; margin-top: 16px; }
  .contact__list li {
    display: flex; align-items: center; gap: 4px;
    font-size: 13px; line-height: 16px;
  }
  .contact__list svg { width: 10px; height: 10px; flex: none; fill: var(--brand-orange); }

  .back-title {
    position: absolute; left: 0; right: 0; top: 98px;
    text-align: center; color: var(--white);
    font-family: "Rubik", sans-serif; font-weight: 700;
  }
  .back-title .main { display: block; font-size: 37px; line-height: 1; letter-spacing: 0.5px; }
  .back-title .sub { display: block; font-size: 19px; letter-spacing: 9px; margin-top: 8px; }
  .tagline {
    position: absolute; left: 0; right: 0; top: 216px;
    text-align: center; color: var(--white);
    font-family: "Open Sans", sans-serif; font-weight: 600; font-size: 13px;
  }
</style>
</head>
<body>
<main class="canvas">
  <section class="card card--front" aria-label="Business card front">
    <div class="brand-block">
      <span class="brand-mark"></span>
      <p class="brand-name">BRIGHTMILL<span class="sub">DATA WORKS</span></p>
    </div>
    <div class="divider"></div>
    <div class="contact">
      <p class="contact__name">MARTIN HALE</p>
      <p class="contact__title">Managing Director</p>
      <ul class="contact__list">
        <li><svg viewBox="0 0 10 10"><path d="M1 3.5C1 2 2.5 1 5 1s4 1 4 2.5V4H7V3H3v1H1z M2 5h6l1 4H1z"/></svg>044-555 018 274</li>
        <li><svg viewBox="0 0 10 10"><path d="M1 2h8v6H1z" /><path d="M1 2l4 3.5L9 2" fill="none" stroke="#f6f6f6" stroke-width="1"/></svg>info@brightmill.com</li>
        <li><svg viewBox="0 0 10 10"><circle cx="5" cy="5" r="4.2"/><path d="M1 5h8M5 1c-2 2-2 6 0 8M5 1c2 2 2 6 0 8" fill="none" stroke="#f6f6f6" stroke-width="0.7"/></svg>www.brightmilldata.com</li>
      </ul>
    </div>
  </section>

  <section class="card card--back" aria-label="Business card back">
    <h1 class="back-title"><span class="main">BRIGHTMILL</span><span class="sub">DATA WORKS</span></h1>
    <p class="tagline">IT HARDWARES AND IT SOLUTIONS</p>
  </section>
</main>
</body>
</html>
```